Print and E-book Personal Injury Front and Back Book Cover

I need a book cover for a personal injury law firm book titled "Steady Ground Ahead" with the subtitle "A Practical Guide for Accident Claims." The book cover should have an image. This isas a lead generation book designed to be give to potential clients to have them sign as new clients.

Target Market(s)

Potential New Clients Looking For a Personal Injury Attorney

Industry/Entity Type

Legal

Requirements
Must have
• Title and some type of image or images

```html
<!DOCTYPE html>
<html lang="en">
<head>
<meta charset="utf-8">
<title>Steady Ground Ahead — Book Cover</title>
<link href="https://fonts.googleapis.com/css2?family=Cabin:wght@700&display=swap" rel="stylesheet">
<style>
  :root {
    --backdrop: #aba49f;
    --cover-navy: #1f4766;
    --title-white: #f2f2f2;
    --photo-light: #e6e4df;
    --photo-green: #8fa68a;
    --photo-road: #9c9d9f;
    --photo-teal: #2a9aa8;
  }
  * { margin: 0; padding: 0; box-sizing: border-box; }
  html, body {
    width: 1162px;
    height: 1200px;
    overflow: hidden;
    background: var(--backdrop);
  }
  .book-cover {
    position: absolute;
    left: 231px;
    top: 55px;
    width: 700px;
    height: 1090px;
    background: var(--cover-navy);
    display: flex;
    flex-direction: column;
    font-family: "Cabin", "Gill Sans", sans-serif;
    font-weight: 700;
    color: var(--title-white);
    text-transform: uppercase;
  }
  .title-band {
    height: 425px;
    display: flex;
    align-items: center;
    padding-left: 155px;
  }
  .book-title {
    font-size: 108px;
    line-height: 1.0;
    letter-spacing: 1px;
  }
  .book-title span { display: block; }
  .cover-photo {
    height: 480px;
    background:
      linear-gradient(180deg, transparent 55%, var(--photo-road) 100%),
      linear-gradient(90deg, var(--photo-green) 0%, var(--photo-light) 45%, var(--photo-light) 60%, var(--photo-teal) 100%);
  }
  .subtitle-band {
    flex: 1;
    display: flex;
    align-items: center;
    justify-content: center;
  }
  .book-subtitle {
    font-size: 40px;
    line-height: 1.25;
    letter-spacing: 0.5px;
    text-align: center;
  }
  .book-subtitle span { display: block; }
</style>
</head>
<body>
  <main class="book-cover">
    <header class="title-band">
      <h1 class="book-title">
        <span>Steady</span>
        <span>Ground</span>
        <span>Ahead</span>
      </h1>
    </header>
    <div class="cover-photo" role="img" aria-label="Photo of a runner sitting on a park road holding an injured bare foot, a sneaker lying beside her, palm trees in soft sunlight behind"></div>
    <footer class="subtitle-band">
      <p class="book-subtitle">
        <span>A Practical Guide for</span>
        <span>Accident Claims</span>
      </p>
    </footer>
  </main>
</body>
</html>
```